Sunset Harbor Living Web Page

We need a web page design that has two intro pages - first being a 'home page', then a link to the second page that has the 'content tabs' and a 'call to action' (see below).

The business helps people that wish to retire to S.E.Asia (Thailand, Malaysia, Indonesia,The Philippines etc) - to enjoy the lifestyle and the remaining years of their lives. What attracts S.E.Asia to many people is the lower cost, the atmoshpere and beauty of the tropics and the vibrancy of the various countries.

People that are wishing to make the most of their retirement and are adventurous at a great bargain compared to the cost of their own countries will be interested.

We help them achieve this - visa, financials (tax, gov't payments etc), introduce them to the right people for property, clubs, retirement facilities, insurance and so forth.

Therefore we are providing an extremely wide ranging service and this site will provide broad but general information only - with a call to action to come and see us for more specific information and how we can help them specifically.

This site will be predominantly for travel and lifestyle, it will be linked with another financial services (financial planning) site later down the track.

The colour scheme is dark green and blue - as per the attached logo design. Photos and background just think lifestyle and S.E.Asia - beaches/mountains/water/recreational activities for retirees.

Target market is mostly those coming up to retirement to those that are already retired. But we also expect to have some interest with younger people that would like to find out more and plan for the future. So a broad age group but I would say mostly 40-70 yrs old.

On the first (Home) page we would like our company name 'Sunset Harbor Living', our logo (which will be on all pages) and a statement such as: “Imagine a retirement where your dreams are brought to life, and you have never felt more alive. Let us show you how”. Then a link to the second page.

We would like an uncluttered site. On the second (contents) page the tabs would be:

- Visa
- Property
- Financials
- Travel
- Insurance & Healthcare
- Medical Tourism
- Cost of living
- Weekly Blogs and articles
- Sunset Harbor Living story

We would also like a call to action on the second page - asking them to leave their contact details if they wish to learn more or sign up to our weekly newsletter/blog.

We are open to suggestions and your imaginations.

Thank you
Malcolm

Font styles to use
Serif
Script

Colors
0255a3
3377b5
00a990
9bcb3c
abd036
33b8a4
85abd2
cadf82
86cfc6

Requirements
Must have
• I have been asked by the web designer to receive a 'Web Font' so that we can 'get off of Zentrofy'. Hope that makes sense.

```html
<!DOCTYPE html>
<html lang="en">
<head>
<meta charset="utf-8">
<title>Sunset Harbor Living</title>
<link rel="stylesheet" href="https://fonts.googleapis.com/css2?family=Great+Vibes&family=Josefin+Slab:wght@400;600;700&family=Open+Sans:wght@400;600&family=Roboto+Slab:wght@400;700&family=Roboto:wght@400;500;700&display=swap">
<style>
:root{
  --blue:#0a97d9;
  --blue-dark:#0a7fc0;
  --green:#1fae5c;
  --green-dark:#17924c;
  --ink:#4a4a4a;
  --muted:#6b6b6b;
  --white:#ffffff;
  --panel:#f3f3f3;
  --dark:#2f2f2f;
  --footer:#2d2d2d;
}
*{box-sizing:border-box;margin:0;padding:0}
html,body{width:1200px;height:2359px;overflow:hidden}
body{position:relative;background:var(--white);font-family:'Open Sans',sans-serif;color:var(--ink)}
.abs{position:absolute}

/* header */
.site-header{position:absolute;left:0;top:0;width:1200px;height:130px;background:var(--white)}
.brand{position:absolute;left:98px;top:36px;display:flex;align-items:center;gap:12px}
.brand-dot{width:44px;height:44px;border-radius:50%;background:var(--green)}
.brand-name{font-family:'Roboto Slab',serif;font-weight:700;font-size:25px;color:var(--blue-dark);line-height:1}
.contact{position:absolute;top:20px;display:flex;align-items:center;gap:12px;font-family:'Josefin Slab',serif;font-size:14px;color:#666;line-height:17px}
.contact .ic{width:34px;height:34px;border-radius:50%;background:var(--blue);display:flex;align-items:center;justify-content:center}
.main-nav{position:absolute;top:77px;right:98px;display:flex;align-items:center;gap:0;font-family:'Josefin Slab',serif;font-size:15px;color:#555}
.main-nav a{display:block;padding:8px 16px 6px;margin-left:14px;text-decoration:none;color:#555}
.main-nav a.active{background:var(--green);color:var(--white);border-radius:3px;padding:8px 12px 6px;margin-left:0}

.sub-nav{position:absolute;left:0;top:130px;width:1200px;height:38px;background:var(--blue);font-family:'Josefin Slab',serif;font-size:15px;color:var(--white)}
.sub-nav a{position:absolute;top:0;height:38px;line-height:40px;color:var(--white);text-decoration:none;white-space:nowrap}
.sub-nav a.active{background:var(--green);padding:0 16px}

/* hero */
.hero{position:absolute;left:0;top:168px;width:1200px;height:458px;overflow:hidden}
.hero-photo{position:absolute;inset:0;background:linear-gradient(90deg,#dfe9f1 0%,#eef1ef 35%,#d9dfe1 55%,#c8b79a 75%,#b9ccd9 100%)}
.hero-title{position:absolute;left:98px;top:50px;font-family:'Great Vibes',cursive;font-size:74px;color:var(--blue);line-height:1}
.hero-text{position:absolute;left:98px;top:186px;width:520px;font-family:'Josefin Slab',serif;font-size:25px;line-height:37px;color:#444}
.hero-cta{position:absolute;left:98px;top:316px;width:316px;height:56px;background:var(--green);border-radius:4px;color:var(--white);font-family:'Josefin Slab',serif;font-size:25px;line-height:58px;text-align:center}
.hero-dots{position:absolute;left:568px;top:423px;display:flex;gap:6px}
.hero-dots span{width:12px;height:12px;border-radius:50%;background:var(--green-dark)}

/* welcome */
.welcome{position:absolute;left:0;top:626px;width:1200px;height:236px;text-align:center;background:radial-gradient(ellipse 520px 24px at 600px 0,rgba(0,0,0,.14),rgba(0,0,0,0))}
.welcome h1{position:absolute;top:28px;width:100%;font-family:'Roboto Slab',serif;font-size:25px;font-weight:700;color:#555}
.welcome h1 em{font-style:normal;color:var(--blue)}
.welcome h2{position:absolute;top:62px;width:100%;font-family:'Roboto Slab',serif;font-size:25px;font-weight:400;color:var(--blue)}
.welcome p{position:absolute;left:165px;top:112px;width:870px;font-size:13px;line-height:24.5px;color:#666}

/* services */
.services{position:absolute;left:0;top:862px;width:1200px;height:437px;background:var(--blue);color:var(--white);text-align:center}
.services h2{position:absolute;top:20px;width:100%;font-family:'Roboto',sans-serif;font-weight:700;font-size:25px}
.services .lead{position:absolute;top:58px;width:100%;font-size:12px}
.svc{position:absolute;top:94px;width:321px}
.svc .photo{height:197px;border:1px solid rgba(255,255,255,.8)}
.svc h3{margin-top:18px;font-family:'Roboto',sans-serif;font-weight:400;font-size:20px;letter-spacing:.5px}
.svc p{margin-top:10px;font-family:'Roboto',sans-serif;font-size:13px;line-height:24px}
.svc p b{font-style:italic}
.arrow{position:absolute;width:34px;height:34px;border-radius:50%;display:flex;align-items:center;justify-content:center}
.services .arrow{background:var(--blue-dark)}

/* story */
.story-photo{position:absolute;left:99px;top:1354px;width:577px;height:362px;background:linear-gradient(180deg,#1a78c9 0%,#5fb0e8 45%,#bfe0ef 62%,#e9dcc2 80%,#d8c8a8 100%)}
.story-card{position:absolute;left:599px;top:1369px;width:497px;height:333px;background:var(--panel);padding:9px}
.story-card .frame{width:100%;height:100%;border:1px solid #6fb7dc;text-align:center}
.story-card h2{margin-top:28px;font-family:'Roboto',sans-serif;font-weight:500;font-size:24px;color:#555}
.story-card h2 em{font-style:normal;color:var(--blue)}
.story-card p{margin:14px auto 0;width:430px;font-family:'Roboto',sans-serif;font-size:12.5px;line-height:24.5px;color:#666}
.read-more{display:inline-block;margin-top:22px;width:107px;height:38px;border:1px solid #aaa;color:var(--green);font-family:'Roboto',sans-serif;font-size:13px;line-height:36px}

/* contact band */
.contact-band{position:absolute;left:0;top:1759px;width:1200px;height:118px;background:linear-gradient(90deg,#4aa4d2 0%,#6ab5dc 60%,#5aa6cf 100%)}
.contact-band h3{position:absolute;left:102px;top:36px;font-family:'Josefin Slab',serif;font-weight:600;font-size:20px;color:var(--white)}
.contact-band p{position:absolute;left:102px;top:63px;font-family:'Roboto',sans-serif;font-size:13px;color:#eaf5fb}
.signup{position:absolute;left:724px;top:33px;width:377px;height:55px;background:var(--white);border-radius:28px;overflow:hidden}
.signup span{position:absolute;left:24px;top:19px;font-style:italic;font-size:13px;color:#aaa}
.signup b{position:absolute;right:0;top:0;width:115px;height:55px;background:var(--green);color:var(--white);font-family:'Roboto',sans-serif;font-weight:500;font-size:15px;line-height:55px;text-align:center}

/* blog */
.blog{position:absolute;left:0;top:1877px;width:1200px;height:423px;background:linear-gradient(180deg,#3b3b3b,#2a2a2a 60%,#3a3a3a)}
.blog h2{position:absolute;top:48px;width:100%;text-align:center;font-family:'Roboto',sans-serif;font-weight:500;font-size:24px;color:var(--white)}
.blog .lead{position:absolute;left:215px;top:96px;width:770px;text-align:center;font-family:'Roboto',sans-serif;font-size:13px;line-height:23px;color:#ddd}
.view-all{position:absolute;left:1022px;top:45px;width:79px;height:36px;background:var(--blue-dark);border-radius:3px;color:var(--white);font-family:'Josefin Slab',serif;font-size:15px;line-height:38px;text-align:center}
.post{position:absolute;top:168px;width:332px;height:201px;border:1px solid #ddd;overflow:hidden}
.post .photo{position:absolute;inset:0}
.post .label{position:absolute;left:0;bottom:0;width:100%;height:37px;background:var(--green);color:var(--white);font-family:'Josefin Slab',serif;font-weight:600;font-size:14px;letter-spacing:.5px;line-height:39px;text-align:center}
.post.feature{background:rgba(40,40,40,.92);color:var(--white);text-align:center}
.post.feature h4{margin-top:24px;font-family:'Josefin Slab',serif;font-weight:600;font-size:15px;letter-spacing:.5px}
.post.feature .meta{margin-top:12px;display:flex;justify-content:center;gap:14px;font-size:12px}
.post.feature p{margin:14px auto 0;width:280px;font-family:'Roboto',sans-serif;font-size:13px;line-height:23px;color:#eee}
.blog .arrow{background:#1c1c1c}

.site-footer{position:absolute;left:0;top:2300px;width:1200px;height:59px;background:var(--footer);color:#ccc;text-align:center;font-family:'Josefin Slab',serif;font-size:14px;line-height:62px}
</style>
</head>
<body>

<header class="site-header">
  <div class="brand"><span class="brand-dot"></span><span class="brand-name">Sunset Harbor Living</span></div>

  <div class="contact" style="left:810px">
    <span class="ic"><svg width="16" height="16" viewBox="0 0 24 24"><path fill="#fff" d="M6.6 10.8c1.4 2.8 3.8 5.1 6.6 6.6l2.2-2.2c.3-.3.7-.4 1-.2 1.1.4 2.3.6 3.6.6.6 0 1 .4 1 1V20c0 .6-.4 1-1 1C10.6 21 3 13.4 3 4c0-.6.4-1 1-1h3.5c.6 0 1 .4 1 1 0 1.3.2 2.5.6 3.6.1.3 0 .7-.2 1z"/></svg></span>
    <span>Call us now on<br>01632 960418</span>
  </div>
  <div class="contact" style="left:968px">
    <span class="ic"><svg width="16" height="16" viewBox="0 0 24 24"><path fill="#fff" d="M3 5h18v14H3z"/><path fill="none" stroke="#0a97d9" stroke-width="2" d="M3 6l9 7 9-7"/></svg></span>
    <span>Email us<br>hello@sunsetharbor.example</span>
  </div>

  <nav class="main-nav">
    <a class="active">Home</a>
    <a>Visa</a>
    <a>Property</a>
    <a>Financials</a>
    <a>Travel</a>
    <a>Contact us</a>
  </nav>
</header>

<nav class="sub-nav">
  <a class="active" style="left:98px">Insurance &amp; Healthcare</a>
  <a style="left:318px">Medical Tourism</a>
  <a style="left:484px">Cost of living</a>
  <a style="left:627px">Weekly Blogs and articles</a>
  <a style="left:845px">Sunset Harbor Living story</a>
  <a style="left:1023px">Contact us</a>
</nav>

<section class="hero">
  <div class="hero-photo" role="img" aria-label="Smiling retired couple embracing on a bright beach"></div>
  <div class="hero-title">Sunset Harbor Living</div>
  <p class="hero-text">We are introduce them to the right people for property, clubs, retirement facilities, insurance and so forth.</p>
  <div class="hero-cta">Subscribe Our Newsletter</div>
  <div class="hero-dots"><span></span><span></span><span></span><span></span></div>
</section>

<section class="welcome">
  <h1>WELCOME TO <em>SHL</em></h1>
  <h2>Sunset Harbor Living</h2>
  <p>Lorem Ipsum is simply dummy text of the printing and typesetting industry. Lorem Ipsum has been the industry's standard dummy text ever since the 1500s, when an unknown printer took a galley of type and scrambled it to make a type specimen book. It has survived not only five centuries, but also the leap into electronic typesetting, remaining essentially unchanged. It was popularised in the 1960s with the release of Letraset sheets containing Lorem Ipsum passages, and more recently with desktop publishing software.</p>
</section>

<section class="services">
  <h2>OUR MAIN SERVICES</h2>
  <div class="lead">We Provide a selection of spcial services</div>

  <div class="arrow" style="left:25px;top:241px"><svg width="12" height="12" viewBox="0 0 12 12"><path d="M8 1L3 6l5 5" fill="none" stroke="#fff" stroke-width="2"/></svg></div>
  <div class="arrow" style="left:1140px;top:241px"><svg width="12" height="12" viewBox="0 0 12 12"><path d="M4 1l5 5-5 5" fill="none" stroke="#fff" stroke-width="2"/></svg></div>

  <article class="svc" style="left:99px">
    <div class="photo" role="img" aria-label="Retired couple sailing a yacht on open sea" style="background:linear-gradient(180deg,#8cc6ec,#dce9f2 55%,#2f73b5)"></div>
    <h3>TRAVEL</h3>
    <p>Lorem Ipsum is simply dummy text of the printing and typesetting industry. Lorem Ipsum has been the industry's standard dummy <b>More Info...</b></p>
  </article>
  <article class="svc" style="left:441px">
    <div class="photo" role="img" aria-label="Cheerful senior couple taking a selfie outdoors" style="background:linear-gradient(135deg,#cfd8d2,#eef0ec 50%,#b7c7b0)"></div>
    <h3>LIFESTYLE</h3>
    <p>Lorem Ipsum is simply dummy text of the printing and typesetting industry. Lorem Ipsum has been the industry's standard dummy <b>More Info...</b></p>
  </article>
  <article class="svc" style="left:782px">
    <div class="photo" role="img" aria-label="Senior couple smiling at a kitchen table with fresh fruit" style="background:linear-gradient(180deg,#e7e1d6,#c9c0ae 55%,#d98c4a)"></div>
    <h3>FINANCIAL SERVICES</h3>
    <p>Lorem Ipsum is simply dummy text of the printing and typesetting industry. Lorem Ipsum has been the industry's standard dummy <b>More Info...</b></p>
  </article>
</section>

<div class="story-photo" role="img" aria-label="Tropical beach with a leaning palm tree under blue sky"></div>
<section class="story-card">
  <div class="frame">
    <h2>SUNSET HARBOR LIVING <em>STORY</em></h2>
    <p>Lorem Ipsum is simply dummy text of the printing and typesetting industry. Lorem Ipsum has been the industry's standard dummy text ever since the 1500s, when an unknown printer took a galley of type and scrambled it to make a type specimen book. It has survived not only five centuries, but also the leap into electronic typesetting, remaining essentially unchanged. It was popularised in the 1960s with the release of Letraset sheets containing Lorem Ipsum passages, and more recently</p>
    <span class="read-more">READ MORE</span>
  </div>
</section>

<section class="contact-band">
  <h3>INTERESTED PEOPLE CAN CONTACT OUR STAFF</h3>
  <p>STAFF WILL PERSONALLY CONTACT YOU TO CONTINUE THE PROCESS</p>
  <div class="signup"><span>Enter Your Email ...</span><b>Subscribe</b></div>
</section>

<section class="blog">
  <h2>RECENT BLOG</h2>
  <div class="view-all">View all</div>
  <p class="lead">The company helps people that wish to retire to S.E.Asia (Thailand, Malaysia, Indonesia,The Philippines etc) - to enjoy the lifestyle and the remaining years of their lives.</p>

  <div class="arrow" style="left:43px;top:252px"><svg width="12" height="12" viewBox="0 0 12 12"><path d="M8 1L3 6l5 5" fill="none" stroke="#fff" stroke-width="2"/></svg></div>
  <div class="arrow" style="left:1122px;top:252px"><svg width="12" height="12" viewBox="0 0 12 12"><path d="M4 1l5 5-5 5" fill="none" stroke="#fff" stroke-width="2"/></svg></div>

  <article class="post" style="left:101px">
    <div class="photo" role="img" aria-label="Smiling senior woman in white on a sunny beach" style="background:linear-gradient(180deg,#9dc6e6,#e8eef2 60%,#e3d6bf)"></div>
    <div class="label">ISLAND &nbsp;LIVING</div>
  </article>
  <article class="post feature" style="left:436px">
    <h4>INDEPENDENT MOON LIVING</h4>
    <div class="meta">
      <span><svg width="10" height="10" viewBox="0 0 10 10"><rect x="0.5" y="1.5" width="9" height="8" fill="none" stroke="#fff"/><path d="M0.5 4h9" stroke="#fff"/></svg> 4-5-2016</span>
      <span><svg width="11" height="10" viewBox="0 0 11 10"><ellipse cx="5.5" cy="4.5" rx="5" ry="4" fill="#fff"/></svg> 2 Comments</span>
      <span><svg width="10" height="10" viewBox="0 0 10 10"><path d="M0 4h2v6H0zM3 4l3-4c1 0 1 1 1 2L6.5 4H10v2l-2 4H3z" fill="#fff"/></svg> 12 Likes</span>
    </div>
    <p>Lorem Ipsum has been the industry's standard dummy text ever since the 1500s, when an unknown printer took a galley of type and scrambled...</p>
  </article>
  <article class="post" style="left:771px">
    <div class="photo" role="img" aria-label="Couple seen from behind watching a sunset" style="background:linear-gradient(180deg,#c9a9c6,#e9c7c0 55%,#6a6f86)"></div>
    <div class="label">ASIA CAMP</div>
  </article>
</section>

<footer class="site-footer">Copyright © 2016 Sunset Harbor Living.All Rights Reserved</footer>

</body>
</html>
```